Trifold Leaflet - Osteopathy

Trifold Leaflet (A4 size paper) to provide information and promote an established English seafront osteopathy clinic.
I would like a simple modern design to reflect the seafront location and the caring nature of osteopathy treatment. The design needs to be not be generic or too corporate.
At the top of the front page in a large font should be the word "Osteopathy" as it will be displayed in a rack of leaflets (photo attached) and needs to be eye-catching.
I have attached a logo file and some examples of the kinds of designs that I like- but i'm very open to your expert ideas!
Also attached is a photo of the location- a bit of an ugly building but right on the beach, it would be great if this location could be emphasized!
The Word files: Leaflets word-inside.doc & Leaflets word-outside.doc uploaded show the content that I'd like- this is definitely not set in stone and I appreciate that less content is probably needed. Feel free to include/leave out whatever you feel is right.
More info on the practice can be found on my website:
www.marlowbayosteo.com
The pixelharbor images are ones that I have previously bought the rights to use, but only use them if you think they suit you design- I have included them i case they are of use to you.
Target Market(s)
Any adult.
Industry/Entity Type
Building
Look and feel

```html
<!DOCTYPE html>
<html lang="en">
<head>
<meta charset="utf-8">
<title>Osteopathy – Leaflet Inside Spread</title>
<link rel="stylesheet" href="https://fonts.googleapis.com/css2?family=Open+Sans:wght@400;600;700&display=swap">
<style>
  :root {
    --orange: #f7a64a;
    --slate: #6f909d;
    --slate-soft: rgba(122, 156, 168, 0.93);
    --teal-head: #6a97a5;
    --grey-text: #9a9a9a;
    --grey-head: #8a8a8a;
    --url: #a9b9bf;
    --white: #ffffff;
  }
  * { box-sizing: border-box; margin: 0; padding: 0; }
  html, body { width: 1200px; height: 860px; overflow: hidden; background: var(--white); }
  body { font-family: "Open Sans", Arial, sans-serif; }
  .spread { position: relative; width: 1200px; height: 860px; overflow: hidden; background: var(--white); }

  .photo-area {
    position: absolute; inset: 0;
    background:
      radial-gradient(ellipse 520px 260px at 420px 640px, rgba(226, 205, 190, 0.75), rgba(255,255,255,0) 70%),
      radial-gradient(ellipse 380px 420px at 1080px 620px, rgba(190, 182, 176, 0.7), rgba(255,255,255,0) 75%),
      linear-gradient(180deg, #ffffff 0%, #ffffff 38%, #f1ece8 58%, #e4ddd7 78%, #d6d0cb 100%);
  }

  .speech { position: absolute; color: var(--white); }
  .speech svg.tail { position: absolute; }

  .intro {
    left: 66px; top: 48px; width: 302px; height: 412px;
    background: var(--orange); border-radius: 16px;
    padding: 14px 17px; font-size: 12px; line-height: 16.4px;
    text-align: justify;
  }
  .intro p { margin-bottom: 16.4px; }
  .intro strong { font-weight: 700; }
  .intro .plain { text-align: left; }
  .intro .treating { margin-bottom: 0; text-align: left; }
  .intro .tail { left: 116px; bottom: -58px; }

  .info-column {
    position: absolute; left: 458px; top: 42px; width: 236px;
    font-size: 11.6px; line-height: 16.5px; color: var(--grey-text);
  }
  .info-column h2 { font-size: 11.6px; font-weight: 700; color: var(--grey-head); margin-bottom: 16.5px; }
  .info-column p { margin-bottom: 16.5px; text-align: justify; }
  .info-column .plain { text-align: left; }
  .info-column strong { color: var(--slate); font-weight: 700; }
  .info-column .recommended { margin-bottom: 0; }
  .info-column .indent { display: block; padding-left: 20px; }
  .info-column .indent-more { display: block; padding-left: 48px; }

  .visit-title {
    position: absolute; left: 888px; top: 40px;
    font-size: 22px; font-weight: 700; color: var(--teal-head); letter-spacing: 0.5px;
  }

  .tab {
    position: absolute; height: 38px; border-radius: 9px;
    color: var(--white); font-weight: 700; font-size: 17px;
    display: flex; align-items: center; justify-content: center;
  }
  .tab .tail { position: absolute; bottom: -13px; }
  .tab-history { left: 825px; top: 87px; width: 228px; background: var(--slate); }
  .tab-history .tail { left: 196px; }
  .tab-assessment { left: 909px; top: 292px; width: 229px; background: var(--orange); }
  .tab-assessment .tail { left: 30px; }
  .tab-treatment { left: 814px; top: 494px; width: 231px; background: var(--slate); }
  .tab-treatment .tail { left: 34px; }

  .step-box {
    position: absolute; background: var(--slate-soft); color: var(--white);
    border-radius: 13px; font-size: 12.2px; line-height: 16.5px; text-align: justify;
    padding: 12px 24px;
  }
  .step-history { left: 811px; top: 150px; width: 358px; height: 132px; }
  .step-assessment { left: 843px; top: 352px; width: 323px; height: 126px; padding-top: 10px; }
  .step-treatment { left: 822px; top: 554px; width: 358px; height: 271px; font-weight: 600; }

  .web-address {
    position: absolute; left: 58px; top: 772px;
    font-size: 23px; letter-spacing: 6px; color: var(--url);
  }
</style>
</head>
<body>
<main class="spread">
  <div class="photo-area" role="img" aria-label="Photograph: a patient lying relaxed on a treatment couch while an osteopath gently supports her head and neck"></div>

  <section class="speech intro">
    <p>Much of the pain and disability we suffer stems from abnormalities in our body's structure and function.</p>
    <p><strong>Osteopathy</strong> treats problems related to the musculoskeletal system, muscles, ligaments, nerves and joints, and helps the body's natural healing ability to correct itself and relieve the pain caused by dysfunction.</p>
    <p>When the body is balanced and efficient, just like a tuned engine, it will function with minimum wear and tear, requiring less energy to operate correctly.</p>
    <p class="plain">Natural, Drug Free, Pain Relief</p>
    <p class="treating">Treating:<br>Arthritis &amp; Joint Pain<br>Back &amp; Neck Pain<br>Frozen Shoulder<br>Sports Injury<br>Sciatica</p>
    <svg class="tail" width="70" height="60" viewBox="0 0 70 60" aria-hidden="true"><path d="M0 0 H70 L36 60 Z" fill="var(--orange)"/></svg>
  </section>

  <section class="info-column">
    <h2>Osteopathy is Regulated and safe</h2>
    <p><strong>Osteopathy</strong> is one of only two complementary and alternative medicines (CAMs) that are regulated under UK law. This regulation works in much the same way as regulation for medical doctors.</p>
    <p>The OSB regulates the Osteopathic profession in the UK, maintaining a Statutory Register of those entitled to practise. Only practitioners meeting the high standards of safety and competency are eligible to join this register. All Osteopaths are required to undertake a certain amount of CPD (Continuing Professional Development) each year to keep up to date with new research and practice within the profession.</p>
    <p class="plain">As Recommended by The Royal Guild of Family Doctors</p>
    <p class="recommended"><strong>Osteopathy</strong> is used to treat many problems related to the musculoskeletal system. Osteopathic manipulation has been recommended by The National Council for Care Excellence (NCCE) and The Royal Guild of Family Doctors <span class="indent">(RGFD) for the treatment of</span><span class="indent-more">low back pain.</span></p>
  </section>

  <h1 class="visit-title">YOUR FIRST VISIT</h1>

  <div class="tab tab-history">Medical History
    <svg class="tail" width="22" height="14" viewBox="0 0 22 14" aria-hidden="true"><path d="M0 0 H22 L4 14 Z" fill="var(--slate)"/></svg>
  </div>
  <p class="step-box step-history">On your first visit, we will ask you lots of questions to build up a detailed medical history. Your past medical history can often be relevant to current problems you are experiencing and may be discussed. We may ask about past illnesses, operations, injuries, accidents and medications.</p>

  <div class="tab tab-assessment">Assessment
    <svg class="tail" width="22" height="14" viewBox="0 0 22 14" aria-hidden="true"><path d="M0 0 H22 L18 14 Z" fill="var(--orange)"/></svg>
  </div>
  <p class="step-box step-assessment">Based on your medical history, we will perform some tests to help form a diagnosis of your current condition. Typical tests include range and quality of joint movements, tenderness to palpation, muscle tone and strength, reflexes and blood pressure.</p>

  <div class="tab tab-treatment">Treatment
    <svg class="tail" width="22" height="14" viewBox="0 0 22 14" aria-hidden="true"><path d="M0 0 H22 L18 14 Z" fill="var(--slate)"/></svg>
  </div>
  <div class="step-box step-treatment">
    <p>Supported by an in depth knowledge of functional anatomy and physiology the detailed examination enables the Osteopath to diagnose safely and choose the right treatment to address the causes of the patient's symptoms. Treatment involves gentle, manual techniques – easing pain, reducing swelling and improving mobility. Osteopathy is a 'package' of care that includes skilled mobilising and manipulative techniques, reinforced by guidance on diet and exercises.</p>
    <p>For further information, or if you have any questions regarding Osteopathy, please contact us. We are here to help.</p>
  </div>

  <p class="web-address">www.marlowbayosteo.com</p>
</main>
</body>
</html>
```